Skincare Clinic specializing in treating difficult skin conditions needs a web design

We want to restructure and rehash our current webdesigns. The current ones are dated and look very old fashioned also, they are not structured well.

The current websites need to get an uplift in look and become more classy and modern with navigation ease by structuring the information into ease of access

The current web address is
www.brightdermhaven.com.au and
www.lumacutis.com.au

We also have international Partner website which is good and we need to better than them. So this website will act as a guide to better the new site
www.dermacalm-drtorvelle.com

But the new site should be more inclined towards a Blue colour or Aqua marine blue orientation and it needs to be Scientific giving authenticity to the medical industry we operate in.

Attached is a webdesign framework and architecture we would want to adopt. It is a schematic diagram and you can creatively adopt based on what you want to propose.

The website needs to be coded and Should be coded in WordPress such that it helps with SEO activity and nexora promoline pickup.

We will need the necessary pictures and we could provide them or agree to by them from the designers source.

Target Market(s)

Patients with Skin Disease and people interested to book consultation or buy products for their Skin condition

Industry/Entity Type

Clinic

Coding

Coded - Design and coding required

Number of Pages Required

5+ page

Font styles to use
Other font styles liked:
• Use a light font denoting class.

Requirements
Must have
• Should be modern, Easy to navigate, mobile friendly and coded in wordpress
• Blue colour and should look scientific and medicinal
Nice to have
• Classy and creative
Should not have
• No Green colour or herbal look

```html
<!DOCTYPE html>
<html lang="en">
<head>
<meta charset="utf-8">
<title>Bright Derm Haven – Skin Clinic</title>
<link href="https://fonts.googleapis.com/css2?family=Open+Sans:wght@300;400;600;700&display=swap" rel="stylesheet">
<style>
:root{
  --blue:#1a85d6;
  --blue-dark:#136cb4;
  --aqua:#2aa9e0;
  --ink:#2b2b2b;
  --text:#3c3c3c;
  --line:#e2e2e2;
  --skin:#e3b89a;
  --skin-light:#f1d6c3;
  --white:#fff;
}
*{margin:0;padding:0;box-sizing:border-box}
html,body{width:819px;height:1200px;overflow:hidden;background:var(--white)}
body{font-family:"Open Sans",Arial,sans-serif;color:var(--text);position:relative}
.abs{position:absolute}

/* header */
.intro-box{left:67px;top:16px;width:328px;height:54px;border:1px solid var(--line);padding:10px 11px;font-size:7.6px;line-height:10.6px;color:#555}
.brand{right:67px;top:24px;display:flex;align-items:center;gap:8px}
.brand-name{font-size:19px;font-weight:600;color:var(--blue);letter-spacing:-.3px;line-height:1}
.brand-dot{width:28px;height:28px;border-radius:50%;background:var(--aqua)}

/* nav */
.main-nav{left:67px;top:82px;width:685px;height:33px;background:var(--blue);border-radius:3px;display:flex;align-items:center;overflow:hidden}
.main-nav a{color:var(--white);text-decoration:none;font-size:9px;height:100%;display:flex;align-items:center;padding:0 15px}
.main-nav a.active{background:var(--blue-dark);padding:0 22px}
.search{position:absolute;right:6px;top:7px;width:146px;height:19px;background:var(--blue-dark);border-radius:2px}
.search svg{position:absolute;right:6px;top:4px}

/* hero */
.hero{left:0;top:115px;width:819px;height:316px;background:linear-gradient(90deg,#e4e4e4,#f1f1f1 55%,#e8e8e8);overflow:hidden}
.hero-main{position:absolute;left:150px;top:0;width:300px;height:316px;background:linear-gradient(180deg,#f3dccb 0%,#e8c2a6 45%,#efd3bf 80%,#ededed 100%)}
.hero-grid{position:absolute;left:150px;top:0;width:300px;height:316px;background:
  linear-gradient(90deg,transparent 49.7%,rgba(255,255,255,.35) 50%,transparent 50.3%),
  linear-gradient(180deg,transparent 32.8%,rgba(255,255,255,.35) 33%,transparent 33.2%,transparent 66.5%,rgba(255,255,255,.35) 66.7%,transparent 67%)}
.tile{position:absolute;border:4px solid var(--white);box-shadow:0 4px 10px rgba(0,0,0,.18);background:linear-gradient(160deg,var(--skin-light),var(--skin) 70%)}
.tile-a{left:100px;top:72px;width:100px;height:112px;transform:rotate(-17deg)}
.tile-b{left:162px;top:170px;width:92px;height:98px;transform:rotate(-6deg);background:linear-gradient(160deg,#efcdb7,#d9a78a)}
.tile-c{left:390px;top:104px;width:102px;height:110px;transform:rotate(9deg)}
.hero-text{left:560px;top:250px;font-size:14.2px;line-height:17.6px;color:#333}
.arrow{width:53px;height:21px;background:#cfcfcf}
.arrow svg{position:absolute;left:13px;top:6px}

/* feature cards */
.card-img{top:483px;width:214px;height:103px;border-bottom:2px solid var(--aqua);overflow:hidden}
.card-label{top:598px;width:214px;display:flex;justify-content:space-between;align-items:baseline}
.card-label b{font-size:11.4px;font-weight:600;color:var(--ink);letter-spacing:.2px}
.card-label span{font-size:8.8px;color:#444}
.consult{left:67px;background:linear-gradient(90deg,#f4ece6 0,#eadfd6 22%,#cfe1e8 38%,#e9f0f2 60%,#f6f6f6 100%)}
.purchase{left:302px;background:linear-gradient(180deg,#1d1d1d,#2f2f2f 55%,#3d3b38)}
.purchase::after{content:"";position:absolute;left:60px;right:30px;bottom:0;height:70px;background:linear-gradient(90deg,#d9dde0,#eef0f0 40%,#c9a24a 75%,#b58d34);opacity:.55}
.practice{left:537px;background:linear-gradient(90deg,#e6edf2,#dde7ef 35%,#f1f4f6 60%,#e8ebee)}

/* about */
h2{font-size:14.2px;font-weight:400;color:var(--ink)}
.body-text{font-size:7.8px;line-height:11px;color:#333;text-align:justify}
.btn{left:67px;top:798px;width:84px;height:21px;background:var(--blue);color:var(--white);font-size:8.6px;display:flex;align-items:center;justify-content:center}
.divider{left:474px;top:668px;height:443px;border-left:1px dotted #bbb}

/* video */
.video{left:67px;top:871px;width:219px;height:136px;background:linear-gradient(135deg,#f2f4f6,#dfe4e8)}
.video-brand{position:absolute;left:10px;top:12px;font-size:17px;font-weight:600;color:var(--blue)}
.video-person{position:absolute;left:4px;top:48px;width:90px;height:88px;background:linear-gradient(180deg,#c9c9c9 0,#d6d6d6 30%,#2d2d35 60%,#1f1f25)}
.video-play{position:absolute;left:99px;top:55px}
.video-caption{position:absolute;left:118px;top:116px;font-size:5px;color:#555;line-height:6px;text-align:center}

/* right column */
.chev{left:732px;top:668px}
.case-img{left:503px;top:693px;width:243px;height:121px;display:flex;gap:2px;background:var(--white)}
.case-img span{flex:1;background:linear-gradient(90deg,#4a3a30,#b9a08e 30%,#d3bcaa 50%,#b9a08e 70%,#4a3a30)}
.avatar{width:62px;height:62px;border-radius:50%;box-shadow:0 0 0 2px #eee}
.t-name{font-size:9.4px;font-weight:600;color:var(--ink)}
.t-date{font-size:6.8px;color:#333;word-spacing:2px}
.t-text{font-size:6.8px;line-height:10.8px;color:#444;width:180px}
.sep{left:501px;width:251px;border-top:1px solid var(--line)}
.view-all{left:712px;top:1073px;font-size:6.8px;color:#333;display:flex;align-items:center;gap:4px}

/* footer */
.footer{left:0;top:1141px;width:819px;height:59px;background:var(--blue);border-top:2px solid var(--aqua)}
.foot-nav{left:0;top:1153px;width:819px;text-align:center;font-size:7.4px;color:var(--white)}
.foot-nav span{margin:0 6px}
.foot-line{left:0;top:1173px;width:819px;border-top:1px solid rgba(255,255,255,.3)}
.copy{left:67px;top:1182px;font-size:7.2px;color:var(--white)}
.social{left:702px;top:1181px;display:flex;gap:7px}
.social i{width:12px;height:12px;border-radius:50%;background:var(--white);display:block}
</style>
</head>
<body>

<header>
  <p class="abs intro-box">Lorem ipsum dolor sit amet, consectetur adipiscing elit. Maecenas ac vehicula ipsum, eget rhoncus leo. Ut sodales magna eget velit volutpat, quis iaculis nunc porta. Nulla porttitor porttitor purus,</p>
  <div class="abs brand"><span class="brand-name">Bright Derm Haven</span><span class="brand-dot"></span></div>
  <nav class="abs main-nav">
    <a class="active">Home</a><a>About Us</a><a>Treatments</a><a>Products</a><a>Results</a><a>Media</a><a>Skin Conditions</a>
    <div class="search"><svg width="11" height="11" viewBox="0 0 11 11"><circle cx="4.5" cy="4.5" r="3.5" fill="none" stroke="#fff" stroke-width="1.3"/><line x1="7" y1="7" x2="10" y2="10" stroke="#fff" stroke-width="1.4"/></svg></div>
  </nav>
</header>

<section class="abs hero">
  <div role="img" aria-label="Collage of framed close-up photos comparing clear skin and skin blemishes">
    <div class="hero-main"></div>
    <div class="hero-grid"></div>
    <div class="tile tile-a"></div>
    <div class="tile tile-b"></div>
    <div class="tile tile-c"></div>
  </div>
</section>
<p class="abs hero-text">Itching to be free of yours<br>psoriasis?<br>Your future is clear with us,<br>naturally</p>
<div class="abs arrow" style="left:0;top:263px"><svg width="27" height="9" viewBox="0 0 27 9"><path d="M27 4.5H2M5 1L1.5 4.5 5 8" fill="none" stroke="#fff" stroke-width="1"/></svg></div>
<div class="abs arrow" style="left:766px;top:269px"><svg width="27" height="9" viewBox="0 0 27 9"><path d="M0 4.5H25M22 1l3.5 3.5L22 8" fill="none" stroke="#fff" stroke-width="1"/></svg></div>

<section class="features">
  <div class="abs card-img consult" role="img" aria-label="Patient consulting with a clinician at a desk"></div>
  <div class="abs card-label" style="left:67px"><b>CONSULTATION</b><span>BOOK ONLINE</span></div>
  <div class="abs card-img purchase" role="img" aria-label="Skincare product bottles and jars"></div>
  <div class="abs card-label" style="left:302px"><b>PURCHASE</b><span>PRODUCTS ONLINE</span></div>
  <div class="abs card-img practice" role="img" aria-label="Practitioner in a white coat with a patient"></div>
  <div class="abs card-label" style="left:537px"><b>PRACTITIONERS</b><span>INTRANET ACCESS</span></div>
</section>

<section class="about">
  <h2 class="abs" style="left:67px;top:663px">About Dr Adrian Torvelle</h2>
  <p class="abs body-text" style="left:67px;top:693px;width:379px">With over 25 years of medical research &amp; clinical practice, Bright Derm Haven is dedicated to on-going research to help our patients achieve the best possible results...so your future is clear with us, naturally! All Bright Derm Haven clinics use the treatment protocols devised by our founder and lead researcher, Dr Adrian Torvelle. The Dermacalm and Velocura range of products are Dr Torvelle's own formulations and are exclusively available from Bright Derm Haven.</p>
  <p class="abs body-text" style="left:67px;top:759px;width:379px">Dr Torvelle constantly reviews the product range in an effort to always be at the cutting edge of current research, both that of Bright Derm Haven as well as medical research all over the world.</p>
  <a class="abs btn">Read More</a>

  <h2 class="abs" style="left:67px;top:839px">What's Unique about our treatment Protocols</h2>
  <div class="abs video">
    <span class="video-brand">Bright Derm Haven</span>
    <div class="video-person" role="img" aria-label="Video still of the clinic founder in a suit"></div>
    <svg class="video-play" width="30" height="30" viewBox="0 0 30 30"><circle cx="15" cy="15" r="14" fill="rgba(255,255,255,.5)" stroke="#222" stroke-width="1.2"/><path d="M12 9l9 6-9 6z" fill="#222"/></svg>
    <span class="video-caption">Dr Adrian Torvelle (PhD)<br>Medical Research Scientist</span>
  </div>
  <p class="abs body-text" style="left:297px;top:869px;width:149px">Our Melbourne team successfully provides patients with treatment for all types and severity of skin conditions - red, itchy or scaly rashes are our specialty.</p>
  <p class="abs body-text" style="left:297px;top:933px;width:149px">With our treatments, you can be confident, as our protocols have been clinically tested and used over many years. We have helped thousands of patients across Melbourne and Australia to achieve outstanding</p>
  <p class="abs body-text" style="left:67px;top:1016px;width:379px">we are one of the world leaders in the treatment of itchy or flaky skin conditions like Psoriasis, Eczema and Dermatitis. Other conditions treated includes Acne, Rosacea, Psoriatic Arthritis, Fungal Nails and Ichthyosis. We have conducted many years of research to identify triggers (diet, lifestyle, chemicals etc) that flare up these conditions.</p>
</section>

<div class="abs divider"></div>

<aside>
  <h2 class="abs" style="left:501px;top:663px">Case Studies</h2>
  <svg class="abs chev" width="17" height="10" viewBox="0 0 17 10"><path d="M5 1L1.5 5 5 9" fill="none" stroke="#555" stroke-width="1.4"/><path d="M12 1l3.5 4L12 9" fill="none" stroke="#1a85d6" stroke-width="1.4"/></svg>
  <div class="abs case-img" role="img" aria-label="Before and after portraits of a patient's skin"><span></span><span></span></div>

  <h2 class="abs" style="left:495px;top:833px">Tesimonials</h2>
  <div class="abs avatar" style="left:495px;top:867px;background:radial-gradient(circle at 50% 45%,#e2b896,#b37a4f 60%,#6e4526)" role="img" aria-label="Portrait of a young man"></div>
  <p class="abs t-name" style="left:572px;top:870px">Jhone doe</p>
  <p class="abs t-date" style="left:572px;top:885px">15-02-2015 &nbsp;| &nbsp;Friday</p>
  <p class="abs t-text" style="left:572px;top:899px">ut nulla eros. Sed vitae commodo nisl. Mauris blandit nisl purus, non vulputate tortor mattis sed. Morbi auctor dictum congue.</p>
  <div class="abs sep" style="top:952px"></div>
  <div class="abs avatar" style="left:495px;top:972px;background:linear-gradient(180deg,#d8876a 0,#d9a285 45%,#2b2b2b 85%)" role="img" aria-label="Portrait of a smiling man in a suit"></div>
  <p class="abs t-name" style="left:572px;top:975px">Jhone doe</p>
  <p class="abs t-date" style="left:572px;top:990px">15-02-2015 &nbsp;| &nbsp;Friday</p>
  <p class="abs t-text" style="left:572px;top:1004px">ut nulla eros. Sed vitae commodo nisl. Mauris blandit nisl purus, non vulputate tortor mattis sed. Morbi auctor dictum congue.</p>
  <div class="abs sep" style="top:1057px"></div>
  <p class="abs view-all">View All <svg width="9" height="9" viewBox="0 0 9 9"><circle cx="4.5" cy="4.5" r="3.8" fill="none" stroke="#555" stroke-width=".8"/><path d="M3 4.5h3M4.8 3.2L6 4.5 4.8 5.8" fill="none" stroke="#555" stroke-width=".8"/></svg></p>
</aside>

<footer>
  <div class="abs footer"></div>
  <p class="abs foot-nav">Home<span>|</span>About Us<span>|</span>Treatments<span>|</span>Products<span>|</span>Results<span>|</span>Media<span>|</span>Skin Conditions</p>
  <div class="abs foot-line"></div>
  <p class="abs copy">© 2015 Yoursite, All rights reserved.</p>
  <div class="abs social"><i></i><i></i><i></i></div>
</footer>

</body>
</html>
```